CoinHarbor.com Site Redesign

We are looking to redesign our CoinHarbor.com site. This site is focused on helping consumers make smart financial decisions. We provide reviews and articles in various categories.

We are looking for a responsive design to run on wordpress. We will also have adsense advertisements on our page and will want some ad spot space. We are thinking of two column design vs. single column.

Here is an example of what our competitors look like:
ShopperBeacon.org (mostly reviews vs. articles)
Homepage - https://www.shopperbeacon.example/
Category Review Listing - https://www.shopperbeacon.example/mortgage-refinance/best-mortgage-refinance
Individual Review - https://www.shopperbeacon.example/mortgage-refinance/c/loan-orchard-mortgage-refinance-review

- I like that the site is extremely clean. I like the fixed header in mobile

PilotGuide
Homepage - https://www.pilotguide.example/
Category Review Listing-https://www.pilotguide.example/auto_insurance/index.php
Individual Review- https://www.pilotguide.example/auto_insurance/drivora_review.php

Articles - https://www.pilotguide.example/blog/2017/11/20/going-on-a-holiday-road-trip-be-prepared-for-these-hazards/

What I Like? I like the two column layout in that it gives room for advertising.
What I Do NOT Like? The top navigation is a little cumbersome and old. Mobile view is not very good. Content seems a bit cluttered.

PennyMoth
Homepage - https://www.pennymoth.example
Category Review Listing - https://www.pennymoth.example/blog/insurance/best-car-insurance-companies/?trk=pm_gn1_4.0
Individual Review- https://www.pennymoth.example/blog/insurance/veloro-insurance-review/

What I Like? very clean. Like the use of white space and focus on bright color call to action buttons.
What I Do NOT Like? In mobile a lot of content is pushed below the fold because of the large image above the fold. Reviews are not well organized.

Target Market(s)

consumers interested in saving money and making smart financial decisions

Industry/Entity Type

Financial

Logo Text

CoinHarbor.com or CoinHarbor

Coding

Coded - Design and coding required

Number of Pages Required

5+ page

Font styles to use
Sans Serif

Colors

Designer to choose colors to be used in the design.

Requirements
Must have
• -responsive design
• -room for ad space in the right column
Nice to have
• -good use of white space
• -clean layouts
Should not have
• -clutter

```html
<!DOCTYPE html>
<html lang="en">
<head>
<meta charset="utf-8">
<title>CoinHarbor – Smart Financial Decisions</title>
<link rel="stylesheet" href="https://fonts.googleapis.com/css2?family=Lato:ital,wght@0,400;0,700;0,900;1,400&display=swap">
<style>
  :root{
    --green:#3a9a1c;
    --green-dark:#1f6e0c;
    --green-deep:#145a07;
    --green-light:#5cbf2a;
    --ink:#333;
    --muted:#666;
    --grey-bg:#ececec;
    --footer-bg:#dcdcdc;
    --white:#fff;
  }
  *{box-sizing:border-box;margin:0;padding:0}
  html,body{width:1200px;height:2688px;overflow:hidden}
  body{font-family:'Lato',Arial,sans-serif;color:var(--ink);background:var(--white)}
  .wrap{width:960px;margin:0 auto;position:relative}

  /* header */
  .site-header{height:112px;background:var(--white)}
  .site-header .wrap{display:flex;align-items:center;justify-content:space-between;height:112px}
  .brand{font-size:32px;font-weight:900;color:var(--green)}
  .main-nav{display:flex;gap:26px}
  .main-nav a{font-size:17px;color:#555;text-decoration:none}

  /* hero */
  .hero{height:488px;position:relative;background:linear-gradient(120deg,#7d8a86 0%,#b9c2c0 40%,#d4d9d6 60%,#8e968f 100%)}
  .hero-photo{position:absolute;inset:0}
  .category-grid{position:absolute;left:120px;top:56px;width:960px;display:grid;grid-template-columns:repeat(4,1fr);gap:8px}
  .category-tile{height:168px;background:rgba(40,140,20,.72);border:2px solid rgba(255,255,255,.45);display:flex;flex-direction:column;align-items:center;justify-content:center;gap:16px;color:var(--white);font-size:14px;font-weight:700;letter-spacing:.5px}
  .category-tile svg{width:64px;height:56px;fill:none;stroke:var(--white);stroke-width:3;stroke-linecap:round;stroke-linejoin:round}

  /* search */
  .search-band{height:80px;background:var(--grey-bg);position:relative}
  .search-bar{position:absolute;left:120px;top:-48px;width:960px;height:128px;background:linear-gradient(90deg,var(--green-dark),var(--green) 55%,var(--green-dark));display:flex;align-items:center;justify-content:center;gap:34px}
  .search-bar h2{color:var(--white);font-size:30px;font-weight:400}
  .search-field{width:380px;height:52px;background:var(--white);display:flex;align-items:center;justify-content:space-between;padding:0 18px;color:#999;font-size:16px}
  .search-field svg{width:16px;height:16px}

  /* why choose */
  .why-choose{height:352px;background:var(--grey-bg)}
  .why-choose .wrap{display:flex;justify-content:space-between;padding-top:30px}
  .why-text{width:470px;padding-top:26px}
  .section-title{font-size:34px;font-weight:700;color:var(--green-deep)}
  .why-text p{font-size:14px;line-height:22px;color:var(--muted);margin-top:20px}
  .why-text p + p{margin-top:12px}
  .btn{display:inline-block;background:var(--green-light);color:var(--white);font-size:14px;font-weight:700;padding:12px 28px;border-radius:24px;margin-top:22px;text-decoration:none}
  .monitor{width:388px;display:flex;flex-direction:column;align-items:center}
  .monitor-screen{width:388px;height:232px;border:12px solid #222;border-radius:6px;background:linear-gradient(135deg,#f4f6fa,#dfe6f0)}
  .monitor-neck{width:70px;height:32px;background:#cfcfcf}
  .monitor-base{width:150px;height:8px;background:#bbb;border-radius:4px}

  /* testimonial */
  .testimonial{height:448px;padding-top:96px}
  .testimonial-band{height:304px;background:linear-gradient(90deg,#5fbc2a,var(--green) 50%,var(--green-dark));position:relative;display:flex;align-items:center;justify-content:center;gap:40px;color:var(--white)}
  .avatar{width:136px;height:136px;border-radius:50%;border:5px solid var(--white);background:linear-gradient(160deg,#8a6a4e,#3e2e22)}
  .quote{width:520px}
  .quote p{font-size:19px;font-style:italic;line-height:28px}
  .quote cite{display:block;margin-top:24px;font-style:normal;font-size:14px}
  .slide-arrow{position:absolute;top:50%;margin-top:-16px;width:20px;height:32px}
  .slide-arrow.prev{left:150px}
  .slide-arrow.next{right:150px}

  /* why check */
  .why-check{height:252px;text-align:center}
  .why-check .section-title{font-size:30px;padding-top:10px}
  .features{display:flex;justify-content:center;gap:40px;margin-top:40px;text-align:left}
  .feature{display:flex;gap:16px;width:260px}
  .feature-icon{flex:none;width:76px;height:76px;border-radius:50%;background:var(--green-deep);border:5px solid #cfe9c3;display:flex;align-items:center;justify-content:center}
  .feature-icon svg{width:34px;height:34px;fill:none;stroke:var(--white);stroke-width:3;stroke-linecap:round;stroke-linejoin:round}
  .feature h3{font-size:18px;font-weight:700;color:#222;margin-top:4px}
  .feature p{font-size:13px;line-height:19px;color:var(--muted);margin-top:6px}

  /* articles */
  .recent-articles{height:480px;background:var(--grey-bg)}
  .recent-articles .section-title{font-size:34px;padding-top:28px;font-weight:400}
  .article-grid{display:flex;gap:40px;margin-top:24px;justify-content:center}
  .article-card{width:290px;background:var(--white);box-shadow:0 1px 3px rgba(0,0,0,.15)}
  .article-image{height:190px;position:relative}
  .article-card:nth-child(1) .article-image{background:linear-gradient(135deg,#c7a786,#7a5a45)}
  .article-card:nth-child(2) .article-image{background:linear-gradient(135deg,#c9b07a,#6e7a3e)}
  .article-card:nth-child(3) .article-image{background:linear-gradient(135deg,#f1c9cf,#b8c7d4)}
  .date-badge{position:absolute;left:50%;bottom:-14px;transform:translateX(-50%);background:var(--green);color:var(--white);font-size:12px;padding:6px 14px}
  .article-body{padding:28px 18px 18px}
  .article-body h3{font-size:18px;font-weight:700;color:#222}
  .article-body p{font-size:12px;line-height:18px;color:var(--muted);margin-top:8px}
  .read-more{display:block;font-size:12px;font-weight:700;color:#222;margin-top:14px}

  /* newsletter */
  .newsletter{height:276px;text-align:center}
  .newsletter h2{font-size:34px;font-weight:400;color:var(--green);padding-top:68px}
  .newsletter p{font-size:15px;color:var(--muted);margin-top:10px}
  .subscribe-form{width:500px;height:50px;margin:24px auto 0;border:1px solid #ccc;border-radius:26px;display:flex;align-items:center;justify-content:space-between;padding:0 6px 0 22px}
  .subscribe-form span{display:flex;align-items:center;gap:10px;color:#888;font-size:15px}
  .subscribe-form span svg{width:18px;height:14px}
  .subscribe-btn{background:var(--green-deep);color:var(--white);font-size:15px;font-weight:700;padding:10px 26px;border-radius:20px}
  .subscribe-form .subscribe-btn{color:var(--white)}

  /* footer */
  .site-footer{height:200px;background:var(--footer-bg);text-align:center;padding-top:44px}
  .footer-nav{display:flex;justify-content:center;gap:24px}
  .footer-nav a{font-size:18px;color:#222;text-decoration:none}
  .social{display:flex;justify-content:center;gap:12px;margin-top:22px}
  .social span{width:28px;height:28px;border-radius:50%;background:#3b5f9c}
  .social span:nth-child(2){background:#2f9fe0}
  .social span:nth-child(3){background:#d2452f}
  .social span:nth-child(4){background:#1d7ab8}
  .social span:nth-child(5){background:#cc2020}
  .copyright{font-size:12px;color:var(--muted);margin-top:20px}
</style>
</head>
<body>

<header class="site-header">
  <div class="wrap">
    <div class="brand">CoinHarbor</div>
    <nav class="main-nav">
      <a href="#">About Us</a><a href="#">Services</a><a href="#">Products</a><a href="#">Why Us</a><a href="#">Testimonials</a><a href="#">Contact Us</a>
    </nav>
  </div>
</header>

<section class="hero">
  <div class="hero-photo" role="img" aria-label="Photo of a man working at a laptop in a bright office"></div>
  <div class="category-grid">
    <div class="category-tile"><svg viewBox="0 0 64 56"><rect x="6" y="10" width="52" height="36" rx="4"/><line x1="6" y1="20" x2="58" y2="20"/><line x1="14" y1="36" x2="28" y2="36"/></svg>CREDIT CARDS</div>
    <div class="category-tile"><svg viewBox="0 0 64 56"><path d="M6 28 32 6l26 22"/><path d="M14 22v28h36V22"/><rect x="27" y="34" width="10" height="16"/></svg>MORTGAGES</div>
    <div class="category-tile"><svg viewBox="0 0 64 56"><ellipse cx="32" cy="14" rx="16" ry="6"/><path d="M16 14v10c0 3 7 6 16 6s16-3 16-6V14"/><path d="M16 24v10c0 3 7 6 16 6s16-3 16-6V24"/><path d="M16 34v10c0 3 7 6 16 6s16-3 16-6V34"/></svg>LOANS</div>
    <div class="category-tile"><svg viewBox="0 0 64 56"><ellipse cx="30" cy="32" rx="20" ry="15"/><line x1="24" y1="20" x2="36" y2="20"/><path d="M20 45v6M40 45v6"/><circle cx="44" cy="28" r="1.5"/></svg>SAVING ACCOUNTS</div>
    <div class="category-tile"><svg viewBox="0 0 64 56"><rect x="14" y="16" width="36" height="32" rx="4"/><path d="M24 16V8h16v8"/><line x1="24" y1="26" x2="24" y2="40"/><line x1="40" y1="26" x2="40" y2="40"/></svg>TRAVEL MONEY</div>
    <div class="category-tile"><svg viewBox="0 0 64 56"><circle cx="32" cy="18" r="10"/><path d="M12 52c2-12 10-18 20-18s18 6 20 18"/></svg>CURRENT ACCOUNTS</div>
    <div class="category-tile"><svg viewBox="0 0 64 56"><path d="M8 38v-8l8-12h32l8 12v8z"/><circle cx="20" cy="40" r="5"/><circle cx="44" cy="40" r="5"/><line x1="8" y1="30" x2="56" y2="30"/></svg>CAR INSURANCE</div>
    <div class="category-tile"><svg viewBox="0 0 64 56"><path d="M6 44h14l14 4 22-10"/><path d="M6 36h12l14 2"/><circle cx="38" cy="16" r="10"/><line x1="38" y1="11" x2="38" y2="21"/></svg>INVESTMENTS</div>
  </div>
</section>

<section class="search-band">
  <div class="search-bar">
    <h2>Looking for Something else?</h2>
    <div class="search-field">Search for check...<svg viewBox="0 0 16 16"><path d="M4 6l4 4 4-4" fill="none" stroke="#666" stroke-width="2"/></svg></div>
  </div>
</section>

<section class="why-choose">
  <div class="wrap">
    <div class="why-text">
      <h2 class="section-title">Why Choose us</h2>
      <p>Helping you compare cards, loans and savings is what we do best. Our team reviews every provider carefully so you can spend less time searching and more time saving for what matters most.</p>
      <p>Clear advice, honest ratings and simple tools help you make smarter money moves every single day.</p>
      <a class="btn" href="#">Read More</a>
    </div>
    <div class="monitor">
      <div class="monitor-screen" role="img" aria-label="Desktop screen showing a financial data chart"></div>
      <div class="monitor-neck"></div>
      <div class="monitor-base"></div>
    </div>
  </div>
</section>

<section class="testimonial">
  <div class="testimonial-band">
    <svg class="slide-arrow prev" viewBox="0 0 20 32"><path d="M16 2 4 16l12 14" fill="none" stroke="#fff" stroke-width="4"/></svg>
    <div class="avatar" role="img" aria-label="Portrait photo of the reviewer"></div>
    <div class="quote">
      <p>" Switching my savings was easy with their clear guides. I found a better rate in minutes and now feel confident about every financial choice I make. "</p>
      <cite>By Dana Whitlow</cite>
    </div>
    <svg class="slide-arrow next" viewBox="0 0 20 32"><path d="M4 2l12 14L4 30" fill="none" stroke="#fff" stroke-width="4"/></svg>
  </div>
</section>

<section class="why-check">
  <h2 class="section-title">Why Check with us?</h2>
  <div class="features">
    <div class="feature">
      <div class="feature-icon"><svg viewBox="0 0 34 34"><circle cx="17" cy="17" r="13"/><path d="M11 17l4 4 8-8"/></svg></div>
      <div><h3>TITLE GOES HERE</h3><p>Short note on why our reviews help you compare offers and pick the right option fast.</p></div>
    </div>
    <div class="feature">
      <div class="feature-icon"><svg viewBox="0 0 34 34"><path d="M6 15h5v14H6zM11 16l6-10c3 0 4 2 3 5l-1 4h8c2 0 3 2 2 4l-3 8c-1 2-2 2-4 2H11"/></svg></div>
      <div><h3>TITLE GOES HERE</h3><p>Short note on why our reviews help you compare offers and pick the right option fast.</p></div>
    </div>
    <div class="feature">
      <div class="feature-icon"><svg viewBox="0 0 34 34"><path d="M4 28h26"/><path d="M6 22l8-8 6 5 10-11"/><path d="M24 8h6v6"/></svg></div>
      <div><h3>TITLE GOES HERE</h3><p>Short note on why our reviews help you compare offers and pick the right option fast.</p></div>
    </div>
  </div>
</section>

<section class="recent-articles">
  <div class="wrap">
    <h2 class="section-title">Recent Articles</h2>
    <div class="article-grid">
      <article class="article-card">
        <div class="article-image" role="img" aria-label="Photo of a couple reviewing finances together"><span class="date-badge">02 Aug 2017</span></div>
        <div class="article-body"><h3>Article Title here</h3><p>A quick summary of the article goes here to give readers an idea of what it covers.</p><a class="read-more" href="#">READ MORE</a></div>
      </article>
      <article class="article-card">
        <div class="article-image" role="img" aria-label="Photo of coins stacked beside a growing plant"><span class="date-badge">02 Aug 2017</span></div>
        <div class="article-body"><h3>Article Title here</h3><p>A quick summary of the article goes here to give readers an idea of what it covers.</p><a class="read-more" href="#">READ MORE</a></div>
      </article>
      <article class="article-card">
        <div class="article-image" role="img" aria-label="Photo of a piggy bank next to a small model house"><span class="date-badge">02 Aug 2017</span></div>
        <div class="article-body"><h3>Article Title here</h3><p>A quick summary of the article goes here to give readers an idea of what it covers.</p><a class="read-more" href="#">READ MORE</a></div>
      </article>
    </div>
  </div>
</section>

<section class="newsletter">
  <h2>Get latest Updates &amp; Newsletters</h2>
  <p>Join our list for weekly money tips and fresh reviews</p>
  <div class="subscribe-form">
    <span><svg viewBox="0 0 18 14"><rect x="1" y="1" width="16" height="12" fill="none" stroke="#888" stroke-width="1.5"/><path d="M1 1l8 7 8-7" fill="none" stroke="#888" stroke-width="1.5"/></svg>Email address</span>
    <span class="subscribe-btn">Subscribe</span>
  </div>
</section>

<footer class="site-footer">
  <nav class="footer-nav">
    <a href="#">Home</a><a href="#">About Us</a><a href="#">Services</a><a href="#">Products</a><a href="#">Why Us</a><a href="#">Testimonials</a><a href="#">Contact Us</a>
  </nav>
  <div class="social"><span></span><span></span><span></span><span></span><span></span></div>
  <p class="copyright">© 2018 CoinHarbor. All rights reserved. Terms of Use</p>
</footer>

</body>
</html>
```